Dental Practice Billboard Design

We are a newer dental practice in need of a simple but appealing billboard for our growing dental practice to attract new patients. The practice is owned by husband and wife dentists and is family friendly in a small town in Kentucky. We try to be very friendly and caring to our patients. Would prefer a blue background for the billboard and our tooth logo to be prominent. We are partial to the Patua One font used in the image below but please feel free to tweak it as you deem necessary. The shape of the uppercase D and lowercase g are why we like that font, so fonts with a similarly shaped “D” and “g” would work as well. Please include our phone number (555) 847-1390. Please see our website Harlowbrookdentistry.example for more info on the practice if needed. Thank you! Looking forward to seeing your creation.
Updates

The dimensions will be 12ft x 24ft (3.6576m x 7.3152m). Apologies for not including this in the original prompt. Thank you all for your submissions.

Industry/Entity Type

Dental

Font styles to use
Other font styles liked:
• Patua One

Colors
0054AA
0677BA
7BADD7
CADEEF
E8F1F8
0094D4
00A9DD
6FCCEA
C7EBF8
E9F6FB
00AB8E
00BBA5
67D7C9
C6EFE9
E9F9F6
59FF00
82FF00
B8FF75
E3FFCB
F4FFEA

Requirements
Must have
• Phone number, website, Logo, Practice name “Harlow Brook Dentistry”
Should not have
• A tagline or slogan

```html
<!DOCTYPE html>
<html lang="en">
<head>
<meta charset="UTF-8">
<title>Harlow Brook Dentistry — Billboard</title>
<link href="https://fonts.googleapis.com/css2?family=Patua+One&display=swap" rel="stylesheet">
<style>
  :root {
    --navy: #062a5c;
    --green: #22ad1f;
    --white: #ffffff;
    --ink: #2b2b2b;
    --rule: #c9d6e8;
    --photo-a: #c9b8a6;
    --photo-b: #3c4656;
  }
  * { box-sizing: border-box; margin: 0; padding: 0; }
  html, body { width: 1200px; height: 730px; overflow: hidden; background: #e9eef4; }
  .billboard {
    position: relative;
    width: 1200px; height: 730px;
    background: var(--navy);
    font-family: "Patua One", Georgia, serif;
    color: var(--white);
    overflow: hidden;
  }
  .photo {
    position: absolute;
    left: 150px; top: 60px;
    width: 250px; height: 290px;
    border-radius: 120px 120px 110px 110px;
    background: linear-gradient(160deg, var(--photo-a) 0%, #e8e2da 45%, var(--photo-b) 100%);
  }
  .practice-name {
    position: absolute;
    left: 440px; top: 70px;
    line-height: 1;
    font-weight: 400;
  }
  .practice-name .primary { display: block; font-size: 112px; letter-spacing: -1px; white-space: nowrap; }
  .practice-name .secondary { display: block; font-size: 76px; margin-top: 14px; margin-left: 4px; }
  .services-heading {
    position: absolute;
    left: 0; right: 0; top: 372px;
    display: flex; align-items: center; justify-content: center; gap: 26px;
    color: var(--green);
    font-size: 40px;
    font-weight: 400;
    text-transform: uppercase;
  }
  .services-heading .rule { width: 300px; height: 2px; background: var(--rule); }
  .services {
    position: absolute;
    left: 70px; top: 440px;
    width: 1080px;
    display: grid;
    grid-template-columns: 260px 300px 300px 220px;
  }
  .services ul { list-style: none; }
  .services li {
    display: flex; align-items: center; gap: 10px;
    font-size: 31px; line-height: 50px;
    white-space: nowrap;
  }
  .tick { width: 22px; height: 22px; flex: none; }
  .contact-bar { position: absolute; left: 0; right: 0; bottom: 0; height: 112px; }
  .web {
    position: absolute; left: 0; top: 0; bottom: 0; width: 680px;
    background: var(--green);
    clip-path: polygon(0 0, 640px 0, 680px 100%, 0 100%);
    display: flex; align-items: center; gap: 16px; padding-left: 28px;
    font-size: 36px;
    white-space: nowrap;
  }
  .phone {
    position: absolute; left: 700px; right: 0; top: 0; bottom: 0;
    background: var(--white);
    clip-path: polygon(0 0, 100% 0, 100% 100%, 40px 100%);
    display: flex; align-items: center; gap: 18px; padding-left: 60px;
    color: var(--ink);
    font-size: 50px;
    white-space: nowrap;
  }
  .icon { width: 48px; height: 48px; flex: none; }
</style>
</head>
<body>
<main class="billboard">
  <div class="photo" role="img" aria-label="Photo of the two dentists in white coats"></div>

  <h1 class="practice-name">
    <span class="primary">Harlow Brook</span>
    <span class="secondary">Dentistry</span>
  </h1>

  <h2 class="services-heading">
    <span class="rule"></span>Our Services<span class="rule"></span>
  </h2>

  <div class="services">
    <ul>
      <li><svg class="tick" viewBox="0 0 22 22"><polyline points="2,12 8,19 20,3" fill="none" stroke="#22ad1f" stroke-width="3"/></svg>Crowns</li>
      <li><svg class="tick" viewBox="0 0 22 22"><polyline points="2,12 8,19 20,3" fill="none" stroke="#22ad1f" stroke-width="3"/></svg>Root Canals</li>
      <li><svg class="tick" viewBox="0 0 22 22"><polyline points="2,12 8,19 20,3" fill="none" stroke="#22ad1f" stroke-width="3"/></svg>Extractions</li>
    </ul>
    <ul>
      <li><svg class="tick" viewBox="0 0 22 22"><polyline points="2,12 8,19 20,3" fill="none" stroke="#22ad1f" stroke-width="3"/></svg>Implants</li>
      <li><svg class="tick" viewBox="0 0 22 22"><polyline points="2,12 8,19 20,3" fill="none" stroke="#22ad1f" stroke-width="3"/></svg>Bridges</li>
      <li><svg class="tick" viewBox="0 0 22 22"><polyline points="2,12 8,19 20,3" fill="none" stroke="#22ad1f" stroke-width="3"/></svg>Clear Aligners</li>
    </ul>
    <ul>
      <li><svg class="tick" viewBox="0 0 22 22"><polyline points="2,12 8,19 20,3" fill="none" stroke="#22ad1f" stroke-width="3"/></svg>Veneers</li>
      <li><svg class="tick" viewBox="0 0 22 22"><polyline points="2,12 8,19 20,3" fill="none" stroke="#22ad1f" stroke-width="3"/></svg>Whitening</li>
      <li><svg class="tick" viewBox="0 0 22 22"><polyline points="2,12 8,19 20,3" fill="none" stroke="#22ad1f" stroke-width="3"/></svg>Fillings</li>
    </ul>
    <ul>
      <li><svg class="tick" viewBox="0 0 22 22"><polyline points="2,12 8,19 20,3" fill="none" stroke="#22ad1f" stroke-width="3"/></svg>Cleanings</li>
      <li><svg class="tick" viewBox="0 0 22 22"><polyline points="2,12 8,19 20,3" fill="none" stroke="#22ad1f" stroke-width="3"/></svg>Dentures</li>
      <li><svg class="tick" viewBox="0 0 22 22"><polyline points="2,12 8,19 20,3" fill="none" stroke="#22ad1f" stroke-width="3"/></svg>OverDentures</li>
    </ul>
  </div>

  <footer class="contact-bar">
    <div class="web">
      <svg class="icon" viewBox="0 0 52 52" aria-hidden="true">
        <circle cx="26" cy="26" r="22" fill="none" stroke="#fff" stroke-width="4"/>
        <ellipse cx="26" cy="26" rx="9" ry="22" fill="none" stroke="#fff" stroke-width="3"/>
        <line x1="4" y1="26" x2="48" y2="26" stroke="#fff" stroke-width="3"/>
      </svg>
      <span>Harlowbrookdentistry.example</span>
    </div>
    <div class="phone">
      <svg class="icon" viewBox="0 0 52 52" aria-hidden="true">
        <path d="M12 6 L20 6 L23 16 L18 20 Q22 30 32 34 L36 29 L46 32 L46 40 Q44 47 36 46 Q12 42 6 16 Q6 8 12 6 Z" fill="#22ad1f"/>
        <path d="M30 8 Q42 10 44 22" fill="none" stroke="#22ad1f" stroke-width="3.5" stroke-linecap="round"/>
        <path d="M29 15 Q36 16 37 23" fill="none" stroke="#22ad1f" stroke-width="3.5" stroke-linecap="round"/>
      </svg>
      <span>(555) 847-1390</span>
    </div>
  </footer>
</main>
</body>
</html>
```